Email Preference Page Design

We are looking for a 2 page design for our users to edit their email preferences and submit friend referrals. You can find the fuctionality, content and text here:

https://brightvanta.mailrelayhub.example/app/linkClick/7281/5fa9c1d3b07e442b/28374615/9bd4e01a7c3f2a65

* the shipping and billing address might be different so you need to show the billing if the "same as shipping" box is not checked. It can auto-hide like the page above shows if that fits your design.

* when the "unsubscribe from all email lists" box is selected, all the other checkbox options will hide as in the example page. We need you to show us what the site will look like with and without that checkbox selected.

We want to match these two pages to the general feel of these website pages:

www.brightvanta.com
and
free.brightvanta.com

The page should be very clean and tight. Project is for design only but must be able to be implemented in html showing button and checkbox states. Technically this must be two pages for our system - one for all the user info and one for individual email referrals (see example above).

Target Market(s)

video professionals

Industry/Entity Type

Shipping

Requirements
Must have
• our logo (see numerous versions attached)
well designed header
well designed sections
clean editable text
tight layout
html friendly
easy to understand
2 pages
Nice to have
• custom checkboxes and radio buttons

```html
<!DOCTYPE html>
<html lang="en">
<head>
<meta charset="utf-8">
<title>BrightVanta – Communication Preferences</title>
<link rel="stylesheet" href="https://fonts.googleapis.com/css2?family=Exo+2:wght@400;500&family=Open+Sans:ital,wght@0,400;0,600;0,700;1,400&display=swap">
<style>
  :root {
    --orange: #f15a2b;
    --navy: #1f3241;
    --ink: #1e2b36;
    --label: #555b61;
    --field-border: #cfd3d6;
    --field-focus: #eef8fb;
    --field-focus-border: #9fb8c4;
    --white: #ffffff;
  }
  * { box-sizing: border-box; margin: 0; padding: 0; }
  html, body { width: 1200px; height: 2532px; overflow: hidden; }
  body {
    position: relative;
    background: var(--white);
    font-family: "Open Sans", Arial, sans-serif;
    color: var(--ink);
  }

  /* header */
  .top-band { position: absolute; left: 0; top: 0; width: 1200px; height: 20px; background: var(--navy); }
  .brand-tab { position: absolute; left: 280px; top: 0; width: 640px; height: 175px; }
  .brand {
    position: absolute; left: 0; top: 40px; width: 1200px;
    display: flex; justify-content: center; align-items: center; gap: 16px;
  }
  .brand-dot { width: 44px; height: 44px; border-radius: 50%; background: var(--orange); }
  .brand-name {
    font-family: "Exo 2", sans-serif; font-weight: 500; font-size: 62px;
    color: #2f3d4a; letter-spacing: 0.5px; line-height: 1;
  }
  .page-title {
    position: absolute; left: 0; top: 200px; width: 1200px; text-align: center;
    font-family: "Exo 2", sans-serif; font-weight: 400; font-size: 70px;
    color: var(--ink); letter-spacing: 0.5px;
  }

  /* section headings */
  .section-head { position: absolute; top: 350px; height: 58px; border-bottom: 2px solid var(--orange); }
  .section-head h2 {
    position: absolute; left: 0; top: 8px;
    font-weight: 600; font-size: 31px; color: var(--orange); line-height: 1.1;
  }
  .section-head .pointer {
    position: absolute; left: 14px; bottom: -12px; width: 0; height: 0;
    border-left: 9px solid transparent; border-right: 9px solid transparent;
    border-top: 10px solid var(--orange);
  }
  .required-badge {
    position: absolute; right: 0; top: 15px; height: 33px; padding: 0 12px;
    background: var(--navy); color: var(--white); border-radius: 3px;
    font-size: 17px; line-height: 33px;
  }
  .contact-head { left: 51px; width: 510px; }
  .shipping-head { left: 641px; width: 507px; }

  /* form fields */
  .field-list { position: absolute; display: flex; flex-direction: column; gap: 7.6px; }
  .field { display: flex; align-items: center; height: 52px; }
  .field-label { text-align: right; font-size: 21px; color: var(--label); padding-right: 12px; flex: none; white-space: nowrap; }
  .contact .field-label { width: 176px; }
  .shipping .field-label { width: 184px; }
  .input {
    height: 52px; border: 1.5px solid var(--field-border); background: var(--white);
    font-size: 20px; color: var(--label); padding-left: 14px; line-height: 49px; flex: none;
  }
  .input.wide { flex: 1; }
  .input.focused { background: var(--field-focus); border-color: var(--field-focus-border); }
  .input.select { position: relative; }
  .input.select::after {
    content: ""; position: absolute; right: 42px; top: 0; width: 1.5px; height: 100%;
    background: var(--field-border);
  }
  .input.select::before {
    content: ""; position: absolute; right: 14px; top: 20px;
    border-left: 8px solid transparent; border-right: 8px solid transparent;
    border-top: 11px solid #9aa0a5;
  }
  .postal-first { width: 139px; }
  .postal-second { width: 169px; }
  .shipping .postal-first { width: 138px; }
  .shipping .postal-second { width: 155px; }
  .postal-plus { width: 38px; text-align: center; font-size: 19px; color: var(--label); flex: none; }

  .contact { left: 38px; top: 456px; width: 522px; }
  .shipping { left: 631px; top: 560px; width: 517px; }

  .same-address {
    position: absolute; left: 638px; top: 450px; display: flex; gap: 12px;
    font-size: 30px; line-height: 37px; color: #3d4750;
  }
  .same-address .box { width: 25px; height: 25px; border: 1.5px solid var(--field-border); margin-top: 6px; flex: none; }

  /* preferences band */
  .prefs { position: absolute; left: 0; top: 1219px; width: 1200px; height: 1283px; background: var(--orange); }
  .prefs-badge {
    position: absolute; left: 557px; top: 1175px; width: 88px; height: 88px;
    border-radius: 50%; background: var(--navy);
  }
  .on-orange { color: var(--white); }
  .check { width: 24px; height: 24px; background: var(--white); flex: none; }
  .subscribe { position: absolute; left: 52px; top: 1340px; }
  .subscribe .main { display: flex; align-items: center; gap: 13px; font-weight: 700; font-size: 28px; }
  .subscribe .note { margin-left: 37px; font-style: italic; font-size: 27px; margin-top: 0; }
  .filter-lead { position: absolute; left: 49px; top: 1431px; font-weight: 700; font-size: 30px; }

  .topic-head {
    position: absolute; top: 1499px; height: 93px;
    border-top: 2.5px solid var(--white); border-bottom: 2.5px solid var(--white);
    font-weight: 600; font-size: 30px; line-height: 29px; padding-top: 12px;
  }
  .topic-head .pointer {
    position: absolute; left: 26px; bottom: -12px;
    border-left: 9px solid transparent; border-right: 9px solid transparent;
    border-top: 10px solid var(--white);
  }
  .topic-head.left { left: 52px; width: 508px; }
  .topic-head.right { left: 635px; width: 511px; }

  .topic-list { position: absolute; top: 1617px; list-style: none; }
  .topic-list li { display: flex; align-items: center; gap: 20px; height: 53.2px; font-size: 21px; white-space: nowrap; }
  .topic-list.left { left: 52px; }
  .topic-list.right { left: 635px; }

  .unsubscribe {
    position: absolute; left: 636px; top: 2061px; width: 507px; height: 64px;
    background: var(--navy); border: 1.5px solid #2f4658;
    display: flex; align-items: center; gap: 12px; padding-left: 16px;
    font-weight: 700; font-size: 27px; white-space: nowrap;
  }
  .submit {
    position: absolute; left: 52px; top: 2356px; width: 360px; height: 76px;
    background: var(--navy); border: 1.5px solid #2f4658;
    text-align: center; line-height: 73px; font-size: 40px; font-weight: 400;
  }
  .bottom-band { position: absolute; left: 0; top: 2502px; width: 1200px; height: 30px; background: var(--navy); }
</style>
</head>
<body>
  <div class="top-band"></div>
  <svg class="brand-tab" viewBox="0 0 640 175" aria-hidden="true">
    <defs>
      <linearGradient id="tabShade" x1="0" y1="0" x2="0" y2="1">
        <stop offset="0" stop-color="#ffffff"/>
        <stop offset="1" stop-color="#f1f2f3"/>
      </linearGradient>
    </defs>
    <path d="M8 0 H632 V135 Q320 188 8 135 Z" fill="#e3e5e7"/>
    <path d="M8 0 H632 V128 Q320 178 8 128 Z" fill="url(#tabShade)"/>
  </svg>
  <div class="brand">
    <span class="brand-dot"></span>
    <span class="brand-name">brightvanta</span>
  </div>
  <h1 class="page-title">Communication Preferences</h1>

  <!-- contact & billing -->
  <div class="section-head contact-head">
    <h2>Contact &amp; Billing</h2>
    <span class="required-badge">Required Fields*</span>
    <span class="pointer"></span>
  </div>
  <div class="field-list contact">
    <div class="field"><span class="field-label">First Name*</span><div class="input wide focused"></div></div>
    <div class="field"><span class="field-label">Last Name*</span><div class="input wide"></div></div>
    <div class="field"><span class="field-label">Email*</span><div class="input wide"></div></div>
    <div class="field"><span class="field-label">Phone</span><div class="input wide"></div></div>
    <div class="field"><span class="field-label">Address 1</span><div class="input wide"></div></div>
    <div class="field"><span class="field-label">Address 2</span><div class="input wide"></div></div>
    <div class="field"><span class="field-label">Address 3</span><div class="input wide"></div></div>
    <div class="field"><span class="field-label">City</span><div class="input wide"></div></div>
    <div class="field"><span class="field-label">Select Country</span><div class="input wide select"></div></div>
    <div class="field"><span class="field-label">State</span><div class="input wide"></div></div>
    <div class="field"><span class="field-label">Postal Code + 4</span><div class="input postal-first">11111</div><span class="postal-plus">+</span><div class="input postal-second">1111</div></div>
  </div>

  <!-- shipping -->
  <div class="section-head shipping-head">
    <h2>Shipping Address</h2>
    <span class="pointer"></span>
  </div>
  <div class="same-address"><span class="box"></span><span>Billing address is same as<br>shipping address</span></div>
  <div class="field-list shipping">
    <div class="field"><span class="field-label">Street Address 1</span><div class="input wide"></div></div>
    <div class="field"><span class="field-label">Street Address 2</span><div class="input wide"></div></div>
    <div class="field"><span class="field-label">Street Address 3</span><div class="input wide"></div></div>
    <div class="field"><span class="field-label">City</span><div class="input wide"></div></div>
    <div class="field"><span class="field-label">Select Country</span><div class="input wide select"></div></div>
    <div class="field"><span class="field-label">State</span><div class="input wide"></div></div>
    <div class="field"><span class="field-label">Postal Code + 4</span><div class="input postal-first">44444</div><span class="postal-plus">+</span><div class="input postal-second">2222</div></div>
  </div>

  <!-- email preferences -->
  <section class="prefs"></section>
  <div class="prefs-badge"></div>

  <div class="subscribe on-orange">
    <div class="main"><span class="check"></span>Subscribe me to your general email list</div>
    <div class="note">This monthly email includes free video loops and VIP sale notices</div>
  </div>
  <p class="filter-lead on-orange">Help us filter our emails so we only sending relevant information to you</p>

  <div class="topic-head left on-orange">Send me emails about these<br>product types:<span class="pointer"></span></div>
  <div class="topic-head right on-orange">Send me emails about these<br>product types:<span class="pointer"></span></div>

  <ul class="topic-list left on-orange">
    <li><span class="check"></span>Low energy motion loops</li>
    <li><span class="check"></span>High energy motion loops</li>
    <li><span class="check"></span>Timelapse footage</li>
    <li><span class="check"></span>Low energy motion loops</li>
    <li><span class="check"></span>High energy motion loops</li>
    <li><span class="check"></span>Timelapse footage</li>
    <li><span class="check"></span>Worship or wedding motion loops</li>
    <li><span class="check"></span>Pre-mixed DVDs and BluRay</li>
    <li><span class="check"></span>Entertainment lasers for concerts and clubs</li>
    <li><span class="check"></span>Entertainment lasers for text &amp; logo display</li>
    <li><span class="check"></span>Custom logo animation services</li>
    <li><span class="check"></span>Video software for creating video animations</li>
    <li><span class="check"></span>Video software for live performance (Vjing)</li>
  </ul>
  <ul class="topic-list right on-orange">
    <li><span class="check"></span>VJing (live performance video)</li>
    <li><span class="check"></span>DJing (live performance audio+video)</li>
    <li><span class="check"></span>Performing in a band</li>
    <li><span class="check"></span>Video editing</li>
    <li><span class="check"></span>Corporate presentations</li>
    <li><span class="check"></span>Worship video services</li>
    <li><span class="check"></span>Lasers for entertainment &amp; branding</li>
    <li><span class="check"></span>Special offers from BrightVanta partners</li>
  </ul>

  <div class="unsubscribe on-orange"><span class="check"></span>Unsubscribe from all email lists</div>
  <div class="submit on-orange">Submit Now</div>

  <div class="bottom-band"></div>
</body>
</html>
```